Visitenkarte für Ergotherapiepraxis
Zielgruppe
Wir arbeiten mit Kindern und Erwachsene jeden Alters.
Diese Personen kommen mit Beeinträchtigungen (körperlich, seelisch, schulisch) im täglichen Leben zu uns. Wir unterstützen unsere Patienten die Beeinträchtigungen zu verringern oder zu kompensieren und so den Alltag besser bewältigen zu können.
Aufgabenstellung
Ein Design was Kinder und Erwachsene anspricht, aber nicht zu verspielt wirkt. Es soll vertrauenserweckend sein. Eventuell sollte die Visitenkarte ein "aufgehendes oder erblühendes oder aufsteigendes" Element enthalten (=zu Beginn war die Beeinträchtigung dann steigt die Lebensqualität als Folge der Behandlung)
Daten vorn:
Ergotherapiepraxis

```html
<!DOCTYPE html>
<html lang="de">
<head>
<meta charset="utf-8">
<title>Visitenkarte Ergotherapiepraxis</title>
<link rel="stylesheet" href="https://fonts.googleapis.com/css2?family=Questrial&display=swap">
<style>
  :root {
    --green-dark: #1f8a1f;
    --green-light: #8cc43c;
    --ink: #1a1a1a;
    --card-top: #ffffff;
    --card-bottom: #f0e2a0;
    --card-border: #d6d6d6;
    --page: #ffffff;
  }
  * { margin: 0; padding: 0; box-sizing: border-box; }
  html, body {
    width: 1047px;
    height: 1200px;
    overflow: hidden;
    background: var(--page);
    font-family: "Questrial", "Century Gothic", sans-serif;
  }
  .card {
    position: absolute;
    left: 16px;
    width: 998px;
    height: 558px;
    border: 2px solid var(--card-border);
    background: linear-gradient(to bottom, var(--card-top) 0%, #fbf6dc 40%, var(--card-bottom) 100%);
    overflow: hidden;
  }
  .card--front { top: 24px; }
  .card--back { top: 607px; }

  .floral-art {
    position: absolute;
    left: 0;
    top: 0;
    width: 440px;
    height: 100%;
    background:
      radial-gradient(ellipse 55% 70% at 20% 85%, rgba(31,138,31,0.55), rgba(31,138,31,0) 70%),
      radial-gradient(ellipse 45% 40% at 40% 40%, rgba(31,138,31,0.25), rgba(31,138,31,0) 70%);
  }

  .contact {
    position: absolute;
    right: 58px;
    top: 0;
    text-align: right;
  }
  .contact__name {
    position: absolute;
    right: 0;
    top: 140px;
    white-space: nowrap;
    font-size: 60px;
    font-weight: 400;
    color: var(--green-dark);
  }
  .contact__practice {
    position: absolute;
    right: 0;
    top: 222px;
    white-space: nowrap;
    font-size: 29px;
    color: var(--green-light);
  }
  .contact__address {
    position: absolute;
    right: 0;
    top: 318px;
    white-space: nowrap;
    font-size: 33px;
    line-height: 46px;
    font-style: italic;
    color: var(--ink);
  }

  .back__title {
    position: absolute;
    left: 0;
    right: 0;
    top: 144px;
    text-align: center;
    font-size: 86px;
    line-height: 110px;
    font-weight: 400;
    color: var(--green-dark);
  }
</style>
</head>
<body>
  <section class="card card--front">
    <div class="floral-art" role="img" aria-label="Aufsteigende grüne Blumenranken mit Blättern als Symbol für wachsende Lebensqualität"></div>
    <div class="contact">
      <h1 class="contact__name">Wilma Roth</h1>
      <p class="contact__practice">Ergotherapiepraxis</p>
      <address class="contact__address">
        Am Lindenweg 12<br>
        15834 Birkenau, OT Lind<br>
        Tel. 033700/41852
      </address>
    </div>
  </section>

  <section class="card card--back">
    <h2 class="back__title">Behandelnder<br>Therapeut</h2>
  </section>
</body>
</html>
```